Bramblewood Card Company Business Cards

We are a trading card store with Glimmorax, sports and other TCG cards, we need a business card design that encompasses a clean cut, modern style with a retro flare. website is bramblewoodcardco.com for reference. Can utilize a comic book era feel or a more modern outdoor feel to utilize the "Pacific Northwest" elements of tress, mountains, etc.

Industry/Entity Type

Trading cards and collectibles

Contact Information for Business Card

business name, email address, phone number, name, owner job title

Font styles to use
Sans Serif

```html
<!DOCTYPE html>
<html lang="en">
<head>
<meta charset="utf-8">
<title>Bramblewood Card Company – Business Cards</title>
<link href="https://fonts.googleapis.com/css2?family=Montserrat:wght@400;600;700&display=swap" rel="stylesheet">
<style>
  :root {
    --page: #ecebe8;
    --card: #ffffff;
    --accent: #1bbde3;
    --slate: #6b6b6b;
    --ink: #1f1f1f;
    --shadow: rgba(0,0,0,0.18);
  }
  * { box-sizing: border-box; margin: 0; padding: 0; }
  html, body { width: 1200px; height: 931px; overflow: hidden; }
  body {
    background: var(--page);
    font-family: "Montserrat", sans-serif;
    display: flex;
    flex-direction: column;
    align-items: center;
    justify-content: center;
    gap: 40px;
  }
  .card {
    position: relative;
    width: 720px;
    height: 411px;
    background: var(--card);
    border-radius: 22px;
    box-shadow: 0 8px 24px var(--shadow);
  }
  .brand {
    display: flex;
    align-items: center;
    gap: 12px;
    color: var(--slate);
    font-weight: 700;
    text-transform: uppercase;
    letter-spacing: 0.04em;
  }
  .brand-dot {
    border-radius: 50%;
    background: var(--accent);
    flex: none;
  }
  .card--front {
    display: flex;
    align-items: center;
    justify-content: center;
  }
  .card--front .brand { font-size: 30px; }
  .card--front .brand-dot { width: 30px; height: 30px; }

  .card--back .brand {
    position: absolute;
    right: 62px;
    top: 78px;
    font-size: 20px;
  }
  .card--back .brand-dot { width: 20px; height: 20px; }
  .divider {
    position: absolute;
    left: 150px;
    right: 70px;
    top: 224px;
    height: 2px;
    background: var(--accent);
  }
  .person {
    position: absolute;
    left: 150px;
    top: 176px;
  }
  .person-name {
    font-size: 38px;
    font-weight: 700;
    color: var(--accent);
    line-height: 1;
  }
  .person-title {
    position: absolute;
    left: 150px;
    top: 234px;
    font-size: 17px;
    color: var(--ink);
  }
  .contacts {
    position: absolute;
    left: 150px;
    top: 272px;
    list-style: none;
    display: flex;
    flex-direction: column;
    gap: 9px;
    font-size: 17px;
    color: var(--ink);
  }
  .contacts li { display: flex; align-items: center; gap: 12px; }
  .contacts svg { width: 18px; height: 18px; flex: none; }
  .address {
    position: absolute;
    right: 62px;
    top: 240px;
    font-size: 16px;
    line-height: 1.35;
    color: var(--ink);
    text-align: left;
  }
</style>
</head>
<body>
  <section class="card card--front">
    <div class="brand"><span class="brand-dot"></span>Bramblewood Card Company</div>
  </section>

  <section class="card card--back">
    <div class="brand"><span class="brand-dot"></span>Bramblewood Card Company</div>
    <div class="person"><h1 class="person-name">Mara Ellison</h1></div>
    <div class="divider"></div>
    <p class="person-title">Owner</p>
    <ul class="contacts">
      <li>
        <svg viewBox="0 0 24 24" aria-hidden="true"><path fill="var(--accent)" d="M6.6 10.8a15.1 15.1 0 0 0 6.6 6.6l2.2-2.2c.3-.3.7-.4 1-.2 1.1.4 2.3.6 3.6.6.6 0 1 .4 1 1V20c0 .6-.4 1-1 1A17 17 0 0 1 3 4c0-.6.4-1 1-1h3.5c.6 0 1 .4 1 1 0 1.3.2 2.5.6 3.6.1.3 0 .7-.2 1z"/></svg>
        06-24681357
      </li>
      <li>
        <svg viewBox="0 0 24 24" aria-hidden="true"><rect x="2" y="5" width="20" height="14" rx="1.5" fill="var(--accent)"/><path d="M3 6l9 7 9-7" fill="none" stroke="#fff" stroke-width="1.6"/></svg>
        info@bramblewoodcardcompany.com
      </li>
      <li>
        <svg viewBox="0 0 24 24" aria-hidden="true"><circle cx="12" cy="12" r="10" fill="var(--accent)"/><path d="M2 12h20M12 2c3 3 3 17 0 20M12 2c-3 3-3 17 0 20" fill="none" stroke="#fff" stroke-width="1.3"/></svg>
        www.bramblewoodcardcompany.com
      </li>
    </ul>
    <address class="address" style="font-style:normal">
      2870 Fernhill Rd Suite 210<br>
      Tacoma, Washington 98402
    </address>
  </section>
</body>
</html>
```